Website redesign for KestrelFinanceMan/TKFinanceMan

Job Title: Talented Web Designer for SEO-Friendly Website Creation & HostFalcon cPanel Integration
 
Inspiration: dunewheelracingexample.com
Pages:

About
Get a Quote
FAQ
Boat Loans
RV Loans
Testimonials
News/Blog
Affiliate Program
Contact

Job Description:
 
We are seeking a skilled and creative freelance web designer to build a stunning, SEO-optimized website for our business. The ideal candidate will have a strong design portfolio, technical expertise in creating search engine-friendly websites, and experience implementing websites into HostFalcon cPanel.
 
Project Overview:
 
Objective: Create a modern, motorsports themed visually appealing website that is optimized for SEO.

Platform: The site will be hosted on HostFalcon, so familiarity with their cPanel for setup and integration is essential.

Deliverables:
         •A fully functional website (desktop and mobile) with user-friendly navigation and a responsive design.
         •SEO best practices implemented throughout, including proper meta tags, optimized images, fast loading speeds, and mobile compatibility.
         •Seamless integration into HostFalcon cPanel for hosting.
         •Guidance or documentation on maintaining the site post-launch.
 
Key Skills Required:
 
         •Proficiency in web design (HTML, CSS, JavaScript, or relevant platforms like WordPress).
         •Knowledge of SEO principles and tools for website optimization.
         •Experience with HostFalcon cPanel, including file management and DNS settings.
         •Strong communication skills to understand our vision and provide progress updates.
 
What We’re Looking For:
 
         •A designer who can transform our ideas into a sleek and functional website.
         •Someone proactive in suggesting creative design elements and SEO improvements.
         •A reliable professional who can meet deadlines and deliver a polished product.
 
Please provide:
 
         1.A brief introduction and why you’re a good fit for this project.
         2.Examples of previous web design projects, especially those with SEO implementation.
         3.Your estimated timeline and cost for this project.
 
We are excited to work with a talented designer who can bring our vision to life. If you are passionate about web design and SEO, we’d love to hear from you!

Target Market(s)

Boat and RV buyers looking for a loan

Coding

Coded - Design and coding required

Number of Pages Required

5+ page

Colors
F0912C
F2A743
F7CA91
FBE8D2
FDF5EE

Requirements
Must have
• motorsports type design
Nice to have
• fcontact forms easy to use layout on brand and color scheme of kestrelfinanceman and tkfinanceman.example

```html
<!DOCTYPE html>
<html lang="en">
<head>
<meta charset="utf-8">
<title>TKFinanceMan.example – RV Loans Made Easy</title>
<link rel="stylesheet" href="https://fonts.googleapis.com/css2?family=Lato:wght@400;700;900&family=Roboto:wght@700;900&display=swap">
<style>
:root{
  --orange:#f26a0c;
  --orange-soft:#fde9da;
  --blue:#2196f3;
  --ink:#141414;
  --text:#555;
  --dark:#121212;
  --white:#fff;
}
*{box-sizing:border-box;margin:0;padding:0}
html,body{width:1200px;height:3747px;overflow:hidden}
body{position:relative;font-family:"Lato",sans-serif;color:var(--text);background:var(--white)}
.abs{position:absolute}
.brand{font-family:"Lato",sans-serif;font-weight:900;color:var(--orange);font-size:26px;letter-spacing:.5px;text-transform:uppercase;display:flex;align-items:center;gap:10px}
.brand i{display:block;width:16px;height:16px;background:var(--orange);border-radius:50%}
.h-head{font-family:"Roboto",sans-serif;font-weight:900;color:var(--ink);text-transform:uppercase;letter-spacing:1px;text-align:center}
.btn{position:absolute;display:flex;align-items:center;justify-content:center;border-radius:30px;color:#fff;font-weight:900;font-size:14px;text-transform:uppercase}
.btn.blue{background:var(--blue)}.btn.orange{background:var(--orange)}

/* header */
.header{top:0;left:0;width:1200px;height:92px;border-top:3px solid var(--orange)}
.contact-chip{position:absolute;top:20px;display:flex;align-items:center;gap:18px}
.chip-icon{width:52px;height:52px;border-radius:50%;background:var(--orange);display:flex;align-items:center;justify-content:center}
.chip-label{font-size:12px;color:#777}
.chip-value{font-size:25px;font-weight:700;color:var(--ink)}
.nav{top:92px;left:0;width:1200px;height:51px;background:var(--blue)}
.nav-home{position:absolute;left:0;top:0;width:205px;height:51px;background:var(--orange);border-radius:0 26px 26px 0}
.nav a{position:absolute;top:17px;color:#fff;font-size:14px;font-weight:700;text-decoration:none;text-transform:uppercase;transform:translateX(-50%)}

/* hero */
.hero{top:143px;left:0;width:1200px;height:494px;background:linear-gradient(100deg,#1c3b33 0%,#21473d 45%,#3a4a48 70%,#5b5f62 100%)}
.hero-tag{left:100px;top:272px;font-size:23px;font-weight:700;color:#fff}
.hero-title{left:100px;top:310px;font-family:"Roboto",sans-serif;font-weight:900;font-size:50px;color:#fff;letter-spacing:2px}
.hero-copy{left:102px;top:375px;font-size:17px;line-height:33px;color:#fff}

/* about */
.about-sub{top:750px;width:1200px;text-align:center;color:var(--orange);font-weight:900;font-size:17px;text-transform:uppercase}
.about-copy{top:788px;width:1200px;text-align:center;font-size:14px;line-height:29px}
.feature{position:absolute;top:874px;width:168px;text-align:center;font-size:15px;line-height:26px;color:#555}
.feature .dot{width:72px;height:72px;border-radius:50%;background:var(--orange-soft);margin:0 auto 14px;display:flex;align-items:center;justify-content:center}
.feature .dot.b{background:#dff0fd}

/* types */
.types-band{top:1348px;left:0;width:1200px;height:600px}
.video{left:150px;top:1100px;width:900px;height:467px;border-radius:30px;background:linear-gradient(180deg,#4d7b9c 0%,#6e9bb6 50%,#a9c6d6 100%);box-shadow:0 10px 30px rgba(0,0,0,.15)}
.play{left:576px;top:1310px;width:48px;height:48px;border-radius:50%;background:var(--orange)}
.type{position:absolute;top:1704px;display:flex;align-items:center;gap:26px}
.type-icon{width:77px;height:77px;border-radius:8px;background:#262626;display:flex;align-items:center;justify-content:center}
.type-name{color:#fff;font-size:16px;font-weight:700;text-transform:uppercase}
.type-link{color:#fff;font-size:13px;font-weight:900;font-style:italic;text-decoration:underline;margin-top:6px}

/* cards */
.card{position:absolute;top:2082px;width:318px;height:426px;background:#fff;box-shadow:0 6px 24px rgba(0,0,0,.08)}
.card-img{position:absolute;top:0;left:0;width:318px;height:224px}
.card h3{position:absolute;left:30px;top:236px;font-size:19px;font-weight:700;color:var(--ink)}
.card p{position:absolute;left:30px;top:272px;width:262px;font-size:12px;line-height:25px;color:#666}
.card .btn{left:30px;top:364px;width:113px;height:34px;font-size:13px;text-transform:none}

/* testimonial */
.quote{top:2760px;left:608px;width:460px;text-align:center;font-size:16px;line-height:30px;color:#555}
.arrow{position:absolute;top:2968px;width:40px;height:40px;border-radius:50%;background:#e2e2e2;display:flex;align-items:center;justify-content:center;font-size:14px;color:#555}

/* footer */
.footer h4{position:absolute;top:3485px;font-family:"Roboto",sans-serif;font-weight:900;color:#fff;font-size:21px;text-transform:uppercase;letter-spacing:1px}
.flist{position:absolute;top:3534px;list-style:none}
.flist li{display:flex;align-items:flex-start;gap:14px;color:#fff;font-size:15px;line-height:32.5px}
.flist .mk{width:12px;flex:none;display:flex;justify-content:center;padding-top:10px}
.copyright{top:3714px;width:1200px;text-align:center;color:#fff;font-size:12px}
</style>
</head>
<body>

<!-- Header -->
<header class="abs header">
  <div class="abs brand" style="left:110px;top:28px"><i></i>TKFinanceMan.example</div>
  <div class="contact-chip" style="left:529px">
    <div class="chip-icon"><svg width="20" height="20" viewBox="0 0 24 24"><path fill="#fff" d="M6.6 10.8c1.4 2.8 3.8 5.1 6.6 6.6l2.2-2.2c.3-.3.7-.4 1-.2 1.1.4 2.3.6 3.6.6.6 0 1 .4 1 1V20c0 .6-.4 1-1 1C10.6 21 3 13.4 3 4c0-.6.4-1 1-1h3.5c.6 0 1 .4 1 1 0 1.3.2 2.5.6 3.6.1.3 0 .7-.2 1z"/></svg></div>
    <div><div class="chip-label">Call Us:</div><div class="chip-value">555-014-2290</div></div>
  </div>
  <div class="contact-chip" style="left:812px">
    <div class="chip-icon"><svg width="20" height="16" viewBox="0 0 24 18"><path fill="#fff" d="M2 0h20c1.1 0 2 .9 2 2v.5l-12 7-12-7V2C0 .9.9 0 2 0zm-2 5l12 7 12-7v11c0 1.1-.9 2-2 2H2c-1.1 0-2-.9-2-2z"/></svg></div>
    <div><div class="chip-label">Email Us:</div><div class="chip-value">tt@tkfinanceman.example</div></div>
  </div>
</header>

<nav class="abs nav">
  <div class="nav-home"></div>
  <a style="left:156px">Home</a>
  <a style="left:259px">About Us</a>
  <a style="left:355px">FAQ</a>
  <a style="left:458px">Boat Loans</a>
  <a style="left:600px">Testimonials</a>
  <a style="left:719px">News</a>
  <a style="left:858px">Affiliate Program</a>
  <a style="left:1021px">Contact Us</a>
</nav>

<!-- Hero -->
<section class="abs hero" role="img" aria-label="Photo of a pontoon boat with an orange canopy cruising on dark green water"></section>
<div class="abs hero-tag">Low Rates, Fast Approvals, Big Adventures</div>
<h1 class="abs hero-title">RV LOANS MADE EASY!</h1>
<p class="abs hero-copy">Welcome to TKFinanceMan.example, your one-stop resource<br>for all of your RV financing needs.</p>
<div class="btn blue" style="left:102px;top:459px;width:139px;height:42px">Get Started</div>
<div class="btn orange" style="left:257px;top:459px;width:198px;height:42px">Calculate Payment</div>
<svg class="abs" style="left:555px;top:604px" width="90" height="34" viewBox="0 0 90 34"><path d="M0 34 C20 34 25 2 45 2 C65 2 70 34 90 34Z" fill="#fff"/><rect x="40" y="14" width="10" height="18" rx="5" fill="none" stroke="#999" stroke-width="1.6"/><path d="M45 18v8m-2.5-2.5L45 26l2.5-2.5" stroke="#999" stroke-width="1.4" fill="none"/></svg>

<!-- About -->
<h2 class="abs h-head" style="top:703px;width:1200px;font-size:34px">About Us</h2>
<div class="abs about-sub">Your trusted source for RV financing.</div>
<p class="abs about-copy">Our goal is to make your RV purchase as quick and stress-free as possible. Our numerous lender relationships allow us<br>to offer competitive rates and terms with quick turn-around times.</p>

<div class="feature" style="left:95px"><div class="dot"><svg width="30" height="30" viewBox="0 0 30 30"><path d="M10 6h10l-2 4c5 2 8 7 8 11 0 5-5 7-11 7S4 26 4 21c0-4 3-9 8-11z" fill="var(--orange)"/><text x="15" y="23" font-size="10" font-weight="900" fill="#fff" text-anchor="middle" font-family="Lato,sans-serif">%</text></svg></div>Loans from $25,000 -<br>$5M</div>
<div class="feature" style="left:264px"><div class="dot b"><svg width="32" height="32" viewBox="0 0 32 32"><circle cx="16" cy="16" r="13" fill="var(--blue)"/><circle cx="16" cy="16" r="8" fill="none" stroke="#fff" stroke-width="2"/><path d="M12 16l3 3 5-6" stroke="#fff" stroke-width="2.4" fill="none"/></svg></div>Up to 25 yrs old</div>
<div class="feature" style="left:432px"><div class="dot"><svg width="32" height="32" viewBox="0 0 32 32"><circle cx="16" cy="16" r="13" fill="var(--orange)"/><rect x="7" y="13" width="18" height="6" rx="1" fill="#fff" transform="rotate(-40 16 16)"/></svg></div>Same-Day Approvals</div>
<div class="feature" style="left:601px"><div class="dot b"><svg width="32" height="32" viewBox="0 0 32 32"><circle cx="16" cy="16" r="13" fill="none" stroke="var(--blue)" stroke-width="4" stroke-dasharray="60 22"/><circle cx="16" cy="16" r="7" fill="var(--blue)"/><text x="16" y="20" font-size="10" font-weight="900" fill="#fff" text-anchor="middle" font-family="Lato,sans-serif">$</text></svg></div>Quick Funding</div>
<div class="feature" style="left:769px"><div class="dot"><svg width="32" height="32" viewBox="0 0 32 32"><circle cx="10" cy="10" r="4" fill="var(--orange)"/><circle cx="22" cy="10" r="4" fill="var(--orange)"/><path d="M3 26c0-6 3-9 7-9s7 3 7 9zm12 0c0-6 3-9 7-9s7 3 7 9z" fill="var(--orange)"/></svg></div>Private Party or<br>Dealer</div>
<div class="feature" style="left:937px"><div class="dot b"><svg width="32" height="32" viewBox="0 0 32 32"><circle cx="16" cy="16" r="13" fill="none" stroke="var(--blue)" stroke-width="2.5" stroke-dasharray="4 3"/><path d="M16 7l2.7 5.6 6.1.8-4.5 4.2 1.1 6-5.4-2.9-5.4 2.9 1.1-6-4.5-4.2 6.1-.8z" fill="var(--blue)"/></svg></div>Best Rates in the<br>Industry</div>
<div class="btn blue" style="left:536px;top:1008px;width:128px;height:40px">Read More</div>

<!-- Types band -->
<svg class="abs types-band" viewBox="0 0 1200 600" preserveAspectRatio="none" role="img" aria-label="Orange-tinted photo of a stone arch bridge over water">
  <path d="M0 0H1200V452L0 592Z" fill="var(--orange)"/>
  <path d="M0 592L1200 452V476L0 596Z" fill="var(--blue)"/>
</svg>
<div class="abs video" role="img" aria-label="Video still of a wake boat with passengers speeding across blue water"></div>
<svg class="abs play" viewBox="0 0 48 48"><circle cx="24" cy="24" r="24" fill="var(--orange)"/><path d="M19 15l14 9-14 9z" fill="#fff"/></svg>
<h2 class="abs h-head" style="top:1622px;width:1200px;font-size:35px;color:#fff">We Finance All Types of RV's</h2>

<div class="type" style="left:97px"><div class="type-icon"><svg width="46" height="30" viewBox="0 0 46 30"><rect x="2" y="4" width="38" height="18" rx="2" fill="var(--orange)"/><rect x="30" y="8" width="14" height="14" rx="2" fill="var(--orange)"/><circle cx="12" cy="24" r="4" fill="#fff"/><circle cx="34" cy="24" r="4" fill="#fff"/></svg></div><div><div class="type-name">Diesel Pushers</div><div class="type-link">APPLY NOW</div></div></div>
<div class="type" style="left:362px"><div class="type-icon"><svg width="46" height="30" viewBox="0 0 46 30"><rect x="4" y="4" width="34" height="18" rx="6" fill="var(--orange)"/><rect x="38" y="18" width="7" height="2" fill="var(--orange)"/><circle cx="18" cy="24" r="4" fill="#fff"/></svg></div><div><div class="type-name">Travel Trailers</div><div class="type-link">APPLY NOW</div></div></div>
<div class="type" style="left:627px"><div class="type-icon"><svg width="40" height="40" viewBox="0 0 40 40"><path d="M20 4v18M20 6l10 6" stroke="var(--orange)" stroke-width="2.5" fill="none"/><path d="M4 24h32l-4 8H8z" fill="var(--orange)"/><path d="M4 36h32" stroke="var(--orange)" stroke-width="2"/></svg></div><div><div class="type-name">Toy Haulers</div><div class="type-link">APPLY NOW</div></div></div>
<div class="type" style="left:893px"><div class="type-icon"><svg width="46" height="30" viewBox="0 0 46 30"><path d="M2 6h30l10 8v8H2z" fill="var(--orange)"/><circle cx="12" cy="24" r="4" fill="#fff"/><circle cx="34" cy="24" r="4" fill="#fff"/></svg></div><div><div class="type-name">Class A, B &amp; C</div><div class="type-link">APPLY NOW</div></div></div>

<!-- More than boats -->
<h2 class="abs h-head" style="top:1977px;width:1200px;font-size:35px">We Finance More Than Just Boats</h2>
<p class="abs" style="top:2029px;width:1200px;text-align:center;font-size:18px;color:#555">At Harborline Recreational Finance, we are your one-stop resource for all marine, RV and Airplane Financing</p>

<div class="card" style="left:103px"><svg class="card-img" viewBox="0 0 318 224" role="img" aria-label="Aerial photo of small boats on a blue lake"><defs><linearGradient id="g1" x1="0" y1="0" x2="0" y2="1"><stop offset="0" stop-color="#3c6f87"/><stop offset="1" stop-color="#1f4c69"/></linearGradient></defs><path d="M0 0H318V224L0 196Z" fill="url(#g1)"/></svg><h3>Marine Financing</h3><p>Lorem ipsum dolor sit amet, consectetur adipiscing elit, sed do eiusmod tempor inci didunt ut labore et dolore magna aliqua.</p><div class="btn blue">Read More</div></div>
<div class="card" style="left:441px"><svg class="card-img" viewBox="0 0 318 224" role="img" aria-label="Photo of a pickup truck towing a boat trailer"><defs><linearGradient id="g2" x1="0" y1="0" x2="0" y2="1"><stop offset="0" stop-color="#7fa8d6"/><stop offset=".55" stop-color="#9a9c9e"/><stop offset="1" stop-color="#c9c5bc"/></linearGradient></defs><path d="M0 0H318V224L0 196Z" fill="url(#g2)"/></svg><h3>RV Financing</h3><p>Lorem ipsum dolor sit amet, consectetur adipiscing elit, sed do eiusmod tempor inci didunt ut labore et dolore magna aliqua.</p><div class="btn orange">Read More</div></div>
<div class="card" style="left:779px"><svg class="card-img" viewBox="0 0 318 224" role="img" aria-label="Photo of a private jet parked on the tarmac"><defs><linearGradient id="g3" x1="0" y1="0" x2="0" y2="1"><stop offset="0" stop-color="#9cc2ea"/><stop offset=".6" stop-color="#e6eaee"/><stop offset="1" stop-color="#b9b7b2"/></linearGradient></defs><path d="M0 0H318V224L0 196Z" fill="url(#g3)"/></svg><h3>Aircraft Financing</h3><p>Lorem ipsum dolor sit amet, consectetur adipiscing elit, sed do eiusmod tempor inci didunt ut labore et dolore magna aliqua.</p><div class="btn blue">Read More</div></div>

<!-- Bottom boat photo -->
<div class="abs" style="left:0;top:3040px;width:1200px;height:440px;background:linear-gradient(180deg,#ffffff 0%,#dbe4ea 40%,#6e8aa0 70%,#2e4d66 100%)" role="img" aria-label="Photo of a red and white pontoon boat speeding across a lake"></div>

<!-- Testimonial -->
<div class="abs" style="left:135px;top:2550px;width:410px;height:410px;border-radius:50%;background:linear-gradient(180deg,#4e8fd6 0%,#d9c49b 35%,#e8e2da 60%,#2f6c67 100%)" role="img" aria-label="Photo of customers riding on a pontoon boat with an orange canopy"></div>
<svg class="abs" style="left:298px;top:2953px" width="84" height="84" viewBox="0 0 84 84"><circle cx="42" cy="42" r="42" fill="var(--orange)"/><path d="M28 34h10v12c0 5-3 8-8 9v-4c2-1 3-3 3-5h-5zm17 0h10v12c0 5-3 8-8 9v-4c2-1 3-3 3-5h-5z" fill="#fff"/></svg>
<h2 class="abs h-head" style="left:600px;top:2648px;width:476px;font-size:35px;line-height:44px">We Let Our Customers<br>Do The Talking</h2>
<p class="abs quote">"Just purchased a boat and used Harborline and they made the process very easy. Dana Whitcombe helped every step of the way and was always available when I had any questions. She was quick to keep me updated and streamlined the entire process of paperwork and funding...</p>
<div class="abs" style="left:600px;top:2920px;width:476px;text-align:center;font-size:18px;font-weight:700;color:var(--ink)">Cal Brenner</div>
<div class="arrow" style="left:792px">&laquo;</div>
<div class="arrow" style="left:843px">&raquo;</div>

<!-- Footer -->
<svg class="abs" style="left:0;top:3352px" width="1200" height="395" viewBox="0 0 1200 395" preserveAspectRatio="none">
  <path d="M0 120L1200 8V395H0Z" fill="var(--dark)"/>
  <path d="M0 120L1200 8V0L0 112Z" fill="var(--orange)"/>
</svg>
<svg class="abs" style="left:1047px;top:3370px" width="52" height="52" viewBox="0 0 52 52"><circle cx="26" cy="26" r="26" fill="var(--blue)"/><path d="M16 20c0-3 3-5 7-5h6c4 0 7 2 7 5v4c0 3-3 5-7 5h-4l-5 4v-4c-2-1-4-3-4-5z" fill="none" stroke="#fff" stroke-width="2"/></svg>

<footer class="footer">
  <div class="abs brand" style="left:110px;top:3521px;font-size:24px"><i></i>TKFinanceMan.example</div>
  <h4 style="left:421px">Quick Links</h4>
  <ul class="flist" style="left:421px">
    <li><span class="mk"><svg width="11" height="11"><circle cx="5.5" cy="5.5" r="5.5" fill="var(--orange)"/><path d="M4.5 3l2.5 2.5-2.5 2.5" stroke="#fff" fill="none"/></svg></span>About</li>
    <li><span class="mk"><svg width="11" height="11"><circle cx="5.5" cy="5.5" r="5.5" fill="var(--orange)"/><path d="M4.5 3l2.5 2.5-2.5 2.5" stroke="#fff" fill="none"/></svg></span>Boat Loans</li>
    <li><span class="mk"><svg width="11" height="11"><circle cx="5.5" cy="5.5" r="5.5" fill="var(--orange)"/><path d="M4.5 3l2.5 2.5-2.5 2.5" stroke="#fff" fill="none"/></svg></span>Testimonials</li>
    <li><span class="mk"><svg width="11" height="11"><circle cx="5.5" cy="5.5" r="5.5" fill="var(--orange)"/><path d="M4.5 3l2.5 2.5-2.5 2.5" stroke="#fff" fill="none"/></svg></span>News/Blog</li>
    <li><span class="mk"><svg width="11" height="11"><circle cx="5.5" cy="5.5" r="5.5" fill="var(--orange)"/><path d="M4.5 3l2.5 2.5-2.5 2.5" stroke="#fff" fill="none"/></svg></span>Affiliate Program</li>
  </ul>
  <h4 style="left:656px">Contact Us</h4>
  <ul class="flist" style="left:656px">
    <li><span class="mk"><svg width="9" height="12" viewBox="0 0 9 12"><path d="M4.5 0C2 0 0 2 0 4.5 0 8 4.5 12 4.5 12S9 8 9 4.5C9 2 7 0 4.5 0z" fill="var(--orange)"/><circle cx="4.5" cy="4.5" r="1.6" fill="var(--dark)"/></svg></span>1480 Harbor Crest Way Ste.<br>210, Port Alden,<br>CA 90000</li>
    <li><span class="mk"><svg width="12" height="12" viewBox="0 0 24 24"><path fill="var(--orange)" d="M6.6 10.8c1.4 2.8 3.8 5.1 6.6 6.6l2.2-2.2c.3-.3.7-.4 1-.2 1.1.4 2.3.6 3.6.6.6 0 1 .4 1 1V20c0 .6-.4 1-1 1C10.6 21 3 13.4 3 4c0-.6.4-1 1-1h3.5c.6 0 1 .4 1 1 0 1.3.2 2.5.6 3.6.1.3 0 .7-.2 1z"/></svg></span>(555) 014-2290</li>
    <li><span class="mk"><svg width="12" height="9" viewBox="0 0 24 18"><path fill="var(--orange)" d="M2 0h20c1.1 0 2 .9 2 2v.5l-12 7-12-7V2C0 .9.9 0 2 0zm-2 5l12 7 12-7v11c0 1.1-.9 2-2 2H2c-1.1 0-2-.9-2-2z"/></svg></span>tt@tkfinanceman.example</li>
  </ul>
  <h4 style="left:943px">Follow Us</h4>
  <ul class="flist" style="left:943px">
    <li><span class="mk"><svg width="11" height="11"><rect width="11" height="11" rx="2" fill="var(--orange)"/></svg></span>Facebook</li>
    <li><span class="mk"><svg width="11" height="11"><rect width="11" height="11" rx="2" fill="var(--orange)"/></svg></span>Instagram</li>
    <li><span class="mk"><svg width="11" height="11"><rect width="11" height="11" rx="2" fill="var(--orange)"/></svg></span>Youtube</li>
  </ul>
  <div class="abs copyright">(C) Copyright 2024 | All Rights Reserved</div>
</footer>

</body>
</html>
```